Business Card Design

New business card design

Target Market(s)

Residential & Commercial Property Managers

Industry/Entity Type

Plumbing Services

Contact Information for Business Card

Name - Rowan Keddle, title - Director, Phone Number - 0431 286 517, email - rowan@tbk-plumbing.com.au, Company ABN - 73 215 904 386,

Font styles to use
Sans Serif

Colors
0054AA
0677BA
7BADD7
CADEEF
E8F1F8

```html
<!DOCTYPE html>
<html lang="en">
<head>
<meta charset="utf-8">
<title>TBK Plumbing – Business Card</title>
<link href="https://fonts.googleapis.com/css2?family=Poppins:wght@300;400;500;700&display=swap" rel="stylesheet">
<style>
  :root {
    --stage: #999999;
    --deep: #0f4a67;
    --sky: #1aa0e6;
    --ink: #16435d;
    --logo-ink: #23272b;
    --paper: #ffffff;
    --pipe-tint: #eef1f3;
  }
  * { margin: 0; padding: 0; box-sizing: border-box; }
  html, body { width: 1200px; height: 547px; overflow: hidden; background: var(--stage); }
  .stage { position: relative; width: 1200px; height: 547px; }
  .card {
    position: absolute; top: 121px; height: 305px; overflow: hidden;
    box-shadow: 0 4px 10px rgba(0,0,0,.45);
    font-family: "Poppins", sans-serif;
  }
  .card--front { left: 58px; width: 535px; }
  .card--back { left: 616px; width: 526px; }
  .card svg.card-art { position: absolute; inset: 0; }
  .wordmark {
    position: absolute; font-family: "Poppins", sans-serif; font-weight: 400;
    color: var(--logo-ink); letter-spacing: 2px; line-height: 1;
  }
  .card--front .wordmark { left: 48px; top: 80px; font-size: 50px; }
  .card--back .wordmark { left: 44px; top: 70px; font-size: 92px; }
  .person-name {
    position: absolute; left: 251px; top: 48px; font-size: 25px; font-weight: 700;
    color: var(--ink); line-height: 1;
  }
  .person-role {
    position: absolute; left: 253px; top: 87px; font-size: 14.5px; font-weight: 500;
    letter-spacing: 2.2px; color: var(--ink); line-height: 1;
  }
  .contact-list { position: absolute; left: 254px; top: 121px; list-style: none; }
  .contact-list li {
    display: flex; align-items: center; gap: 8px; height: 26px;
    font-size: 14px; color: var(--ink);
  }
  .contact-icon { width: 17px; height: 17px; flex: none; }
  .abn {
    position: absolute; left: 0; right: 0; top: 250px; text-align: center;
    font-size: 16px; color: var(--paper); padding-left: 180px;
  }
  .abn-label { color: var(--sky); }
</style>
</head>
<body>
<main class="stage">

  <section class="card card--front">
    <svg class="card-art" width="535" height="305" viewBox="0 0 535 305">
      <defs>
        <linearGradient id="pipeTintFront" x1="0" y1="0" x2="1" y2="1">
          <stop offset="0" stop-color="#f3f5f6"/>
          <stop offset="1" stop-color="#ffffff"/>
        </linearGradient>
      </defs>
      <rect class="deep-band" width="535" height="305" fill="var(--deep)"/>
      <path class="wave-edge" d="M0,6 C25,126 60,196 120,221 C180,246 250,221 330,216 C400,211 460,226 535,255 V0 H0 Z" fill="var(--sky)"/>
      <path class="light-field" d="M0,0 H535 V247 C460,220 400,205 330,210 C250,215 180,240 120,215 C60,190 25,120 0,0 Z" fill="url(#pipeTintFront)" role="img" aria-label="Faint background of white plumbing pipes"/>
    </svg>
    <div class="wordmark">TBK</div>
    <h1 class="person-name">Rowan Keddle</h1>
    <p class="person-role">DIRECTOR</p>
    <ul class="contact-list">
      <li>
        <svg class="contact-icon" viewBox="0 0 20 20"><circle cx="10" cy="10" r="10" fill="var(--sky)"/><path d="M7 5.5l1.6 2.4-1 1.1c.6 1.3 1.5 2.2 2.6 2.7l1.1-1 2.3 1.6-.8 1.8c-3.6-.2-6.4-3.1-6.6-6.7z" fill="#fff"/></svg>
        <span>0431 286 517</span>
      </li>
      <li>
        <svg class="contact-icon" viewBox="0 0 20 20"><circle cx="10" cy="10" r="10" fill="var(--sky)"/><rect x="5" y="6.5" width="10" height="7" rx="1" fill="#fff"/><path d="M5.5 7l4.5 3.5L14.5 7" stroke="var(--sky)" stroke-width="1.2" fill="none"/></svg>
        <span>rowan@tbk-plumbing.com.au</span>
      </li>
    </ul>
    <p class="abn"><span class="abn-label">ABN</span> - 73 215 904 386</p>
  </section>

  <section class="card card--back">
    <svg class="card-art" width="526" height="305" viewBox="0 0 526 305">
      <defs>
        <linearGradient id="pipeTintBack" x1="0" y1="0" x2="1" y2="1">
          <stop offset="0" stop-color="#f3f5f6"/>
          <stop offset="1" stop-color="#ffffff"/>
        </linearGradient>
      </defs>
      <rect class="deep-band" width="526" height="305" fill="var(--deep)"/>
      <path class="wave-edge" d="M0,0 H526 V28 C520,108 500,198 430,218 C320,233 200,208 120,223 C70,233 30,243 0,253 Z" fill="var(--sky)"/>
      <path class="light-field" d="M0,0 H526 V20 C520,100 500,190 430,210 C320,225 200,200 120,215 C70,225 30,235 0,245 Z" fill="url(#pipeTintBack)" role="img" aria-label="Faint background of white plumbing pipes"/>
      <circle class="accent-disc" cx="424" cy="150" r="82" fill="var(--sky)" stroke="var(--paper)" stroke-width="5"/>
    </svg>
    <div class="wordmark">TBK</div>
  </section>

</main>
</body>
</html>
```